Coffee and Plastics

I am looking for a completely new site that shows the products we have. Our current site is www.velmorebrothersbeans.com. We are open minded to what designers come up with. Our current site is www.velmorebrothersbeans.com. You can you the information from there to start the site. I need these tabs on the main home page. ( Home, Coffee & Tea, Condiments, and Paper and Plastics, and Contact.) You can take photos and info from my Current site. In products page.
I will be uploading info and photo for paper and plastics.
Look and feel
Each slider illustrates characteristics of the customer's brand and the style your logo design should communicate.

```html
<!DOCTYPE html>
<html lang="en">
<head>
<meta charset="utf-8">
<title>Velmore Brothers Beans</title>
<link href="https://fonts.googleapis.com/css2?family=Marcellus&family=Mako&family=Open+Sans:wght@400;600&display=swap" rel="stylesheet">
<style>
:root{
  --bean-dark:#5a2a08;
  --bean-mid:#a0500c;
  --bean-light:#d27a1f;
  --nav-top:#8a4a08;
  --nav-bottom:#5c2f05;
  --title-brown:#6b3a0c;
  --accent-orange:#c8731c;
  --welcome-red:#8b1a2b;
  --heading-brown:#7a3d12;
  --text-grey:#555;
  --text-dark:#333;
  --footer-bg:#5e2e04;
  --white:#fff;
}
*{margin:0;padding:0;box-sizing:border-box}
html,body{width:1044px;height:1200px;overflow:hidden}
body{position:relative;font-family:"Open Sans",sans-serif;background:var(--bean-mid)}
.backdrop{position:absolute;inset:0;background:linear-gradient(180deg,#b4560f 0%,#a24d0b 45%,#9c4a06 100%)}
.page{position:absolute;left:118px;top:0;width:809px;height:1200px;background:var(--white)}
.site-header{position:absolute;left:0;top:0;width:809px;height:89px}
.site-title{position:absolute;left:0;width:809px;top:36px;text-align:center;font-family:"Marcellus",serif;font-size:31px;color:var(--title-brown);font-weight:400}
.call{position:absolute;right:20px;top:37px;text-align:right;font-family:"Mako",sans-serif;color:var(--accent-orange)}
.call-label{font-size:16px;line-height:18px}
.call-number{font-size:18px;line-height:22px;color:#a8590e;font-weight:600}
.main-nav{position:absolute;left:0;top:89px;width:809px;height:44px;background:linear-gradient(180deg,var(--nav-top),var(--nav-bottom));display:flex;justify-content:center}
.main-nav a{color:var(--white);text-decoration:none;font-family:"Mako",sans-serif;font-size:15px;line-height:44px;padding:0 26px;border-left:1px solid rgba(255,255,255,.18)}
.main-nav a:first-child{border-left:none}
.hero{position:absolute;left:0;top:133px;width:809px;height:349px;background:radial-gradient(ellipse at 60% 60%,#6b3716 0%,#3b1c0a 55%,#9b6a3c 100%)}
.hero-dots{position:absolute;left:381px;top:463px;display:flex;gap:3px}
.hero-dots span{width:10px;height:10px;border-radius:50%;background:var(--white)}
.welcome{position:absolute;left:40px;top:508px;width:729px;text-align:center}
.welcome h1{font-family:"Mako",sans-serif;font-weight:400;font-size:24px;color:var(--welcome-red);margin-bottom:10px}
.welcome p{font-size:10.4px;line-height:18px;color:var(--text-grey);margin-bottom:4px}
.panels{position:absolute;left:0;top:676px;width:809px;height:220px;background:linear-gradient(180deg,#f6f2ee 0%,#fff 60%)}
.col{position:absolute;top:40px}
.col h2{font-family:"Mako",sans-serif;font-weight:400;font-size:20px;color:var(--heading-brown);margin-bottom:10px}
.post h3,.feature h3{font-weight:400;font-size:13px;color:var(--text-dark);margin-bottom:2px}
.post p,.feature p{font-size:9.6px;line-height:16px;color:var(--text-grey)}
.post{margin-bottom:12px}
.blog{left:35px;width:210px}
.products{left:274px}
.thumbs{display:grid;grid-template-columns:repeat(3,74px);gap:8px 7px}
.thumb{width:74px;height:66px;border:1px solid #ccc}
.t1{background:linear-gradient(#6b6b6b,#3a3a3a)}
.t2{background:radial-gradient(#f2f2f2,#9a9a9a)}
.t3{background:radial-gradient(#d8b85a,#6b5220)}
.t4{background:radial-gradient(#fafafa,#b86c3a)}
.t5{background:linear-gradient(90deg,#eaeaea,#8a6a4a)}
.t6{background:radial-gradient(#d0d0d0,#3c3c3c)}
.coffee{left:546px;width:236px}
.feature-img{width:226px;height:91px;background:radial-gradient(ellipse at 65% 55%,#f4efe8 0%,#7a3a18 40%,#3a1a0a 100%);margin-bottom:6px;margin-left:2px}
.feature{padding-left:2px}
.partners{position:absolute;left:0;top:960px;width:809px}
.badge-row{display:flex;justify-content:center;align-items:center;gap:20px;margin-bottom:16px}
.badge{height:40px;border-radius:8px;border:2px solid #ddd}
.site-footer{position:absolute;left:0;top:1110px;width:809px;height:90px;background:var(--footer-bg)}
.footer-nav{position:absolute;left:36px;top:24px;font-size:12.5px;color:var(--white)}
.footer-nav a{color:var(--white);text-decoration:none}
.footer-nav .sep{margin:0 8px}
.copyright{position:absolute;left:36px;top:47px;font-size:10px;color:#f2e3d0}
.social{position:absolute;left:697px;top:23px;display:flex;gap:3px}
.social span{width:24px;height:24px;border-radius:50%;background:var(--white)}
</style>
</head>
<body>
<div class="backdrop" role="img" aria-label="Warm orange backdrop of roasted coffee beans"></div>
<div class="page">
  <header class="site-header">
    <div class="site-title">Velmore Brothers Beans</div>
    <div class="call">
      <div class="call-label">Call Us Now</div>
      <div class="call-number">1-800-555-0142</div>
    </div>
  </header>
  <nav class="main-nav">
    <a href="#">Home</a><a href="#">Coffee &amp; Tea</a><a href="#">Condiments</a><a href="#">Paper</a><a href="#">Plastics</a><a href="#">Contact</a>
  </nav>
  <div class="hero" role="img" aria-label="Wooden scoop spilling roasted coffee beans beside a burlap sack"></div>
  <div class="hero-dots"><span></span><span></span><span></span><span></span></div>

  <section class="welcome">
    <h1>Welcome to Velmore Brothers Beans</h1>
    <p>We are a family-owned and operated business based in Marlow Creek Texas. Since the opening of Velmore Brothers Beans plant in 1995, we have become Texas' premier independently owned coffee packaging company. Our success relies solely on the principle of selling only the freshest, highest-quality in-room coffee available.&nbsp; Velmore Brothers packages and supplies in-room coffee, tea products, and condiments.</p>
    <p>Whether we're supplying a 50-room Hotel or a 500-room grand resort, we have the distribution capacity to fill your rooms with the most aromatic and robust coffees and teas available at competitive prices.</p>
  </section>

  <section class="panels">
    <div class="col blog">
      <h2>Recent Blog Post</h2>
      <div class="post"><h3>Mauris vel lacus vitae</h3><p>Aliquam nec erat at purus cursus interdum Vestibulum ligula augue bibendum</p></div>
      <div class="post"><h3>Pellentesque faucibus</h3><p>Donec convallis pede venenatis nibh Duis quam Nam eget lacus Aliquam erat volutpat Quisque dignissim congue leo</p></div>
    </div>
    <div class="col products">
      <h2>Our Products</h2>
      <div class="thumbs">
        <div class="thumb t1" role="img" aria-label="Gold plastic fork and spoon"></div>
        <div class="thumb t2" role="img" aria-label="White divided plastic tray"></div>
        <div class="thumb t3" role="img" aria-label="Gold plastic serving tray"></div>
        <div class="thumb t4" role="img" aria-label="Clear plastic cup"></div>
        <div class="thumb t5" role="img" aria-label="Paper coffee cup with lid"></div>
        <div class="thumb t6" role="img" aria-label="Clear divided platter"></div>
      </div>
    </div>
    <div class="col coffee">
      <h2>Coffe &amp; Tea</h2>
      <div class="feature-img" role="img" aria-label="Cup of black coffee on scattered beans"></div>
      <div class="feature"><h3>Aliquam nec erat at purus</h3><p>Aliquam nec erat at purus cursus interdum Vestibu-lum ligula augue bibendum accumsan</p></div>
    </div>
  </section>

  <section class="partners" aria-label="Hotel partners">
    <div class="badge-row">
      <div class="badge" style="width:58px;background:#2a9a3a"></div>
      <div class="badge" style="width:56px;background:#2c2a6a"></div>
      <div class="badge" style="width:56px;background:#1c3a7a"></div>
      <div class="badge" style="width:60px;background:#1f5a3a"></div>
      <div class="badge" style="width:56px;background:#1e7a44"></div>
      <div class="badge" style="width:58px;background:#1c2e7a"></div>
      <div class="badge" style="width:40px;background:#1c5a3a"></div>
      <div class="badge" style="width:56px;background:#2a3aa0"></div>
    </div>
    <div class="badge-row">
      <div class="badge" style="width:62px;background:#f6f3d8"></div>
      <div class="badge" style="width:40px;background:#1c4a9a"></div>
      <div class="badge" style="width:46px;background:#1c2a7a"></div>
      <div class="badge" style="width:52px;background:#2a6a3a"></div>
      <div class="badge" style="width:40px;background:#b8162a"></div>
      <div class="badge" style="width:46px;background:#1c2060"></div>
      <div class="badge" style="width:88px;background:#f4f0f0"></div>
      <div class="badge" style="width:54px;background:#fafafa"></div>
    </div>
  </section>

  <footer class="site-footer">
    <nav class="footer-nav">
      <a href="#">Home</a><span class="sep">|</span><a href="#">Coffee &amp; Tea</a><span class="sep">|</span><a href="#">Condiments</a><span class="sep">|</span><a href="#">Paper</a><span class="sep">|</span><a href="#">Plastics</a><span class="sep">|</span><a href="#">Contact</a>
    </nav>
    <div class="copyright">© 2014 Company Name.&nbsp; All right reserved.&nbsp; Term of Use</div>
    <div class="social" aria-label="Social links"><span></span><span></span><span></span></div>
  </footer>
</div>
</body>
</html>
```